Satchel & Sundial needs new business card design

I need a new business card design. I'm looking for out-of-the-box design which represents the freedom of being a location independent entrepreneur.
I offer coaching, retreats and trips.
I would like to see designs with and without the photo.
Colors I use are black (#000000), green (#25A796) and brown (#D7C38C)
Website satchelandsundial.example

Target Market(s)

location independent entrepreneurs, digital nomads, people looking to swap the 9 to 5 for a lifestyle business

Industry/Entity Type

Business

Contact Information for Business Card

Dorota Falkner
Your Lifestyle Business Coach, Retreat & Trip Leader
http://satchelandsundial.example
hello@satchelandsundial.example
Live a life you don't need a holiday from

Font styles to use
Serif
Sans Serif

Requirements
Must have
• One side should contain only the logo. I would also consider having the "Live a life you don't need a holiday from" on that side too (depending on how it looks)
• Please show both sides on the designs.

```html
<!DOCTYPE html>
<html lang="en">
<head>
<meta charset="utf-8">
<title>Satchel &amp; Sundial — Business Card</title>
<link href="https://fonts.googleapis.com/css2?family=Source+Sans+3:wght@400;600&display=swap" rel="stylesheet">
<style>
  :root {
    --ink: #111111;
    --green: #25a796;
    --paper: #ffffff;
    --rule: #9a9a9a;
    --stage-top: #2b2b2b;
    --stage-bottom: #050505;
  }
  * { margin: 0; padding: 0; box-sizing: border-box; }
  html, body { width: 1200px; height: 900px; overflow: hidden; }
  body {
    position: relative;
    background: linear-gradient(to bottom, var(--stage-top), var(--stage-bottom));
    font-family: "Source Sans 3", Arial, sans-serif;
  }
  .card {
    position: absolute;
    top: 306px;
    width: 440px;
    height: 271px;
    border-radius: 12px;
  }
  .card--front { left: 149px; background: var(--paper); }
  .card--back { left: 608px; background: var(--green); }

  .tagline {
    position: absolute; top: 20px; left: 0; right: 0;
    text-align: center; font-size: 12.5px; color: var(--green);
    text-transform: uppercase; letter-spacing: 0.1px;
  }
  .wordmark {
    position: absolute; left: 0; right: 0;
    text-align: center; font-weight: 600; text-transform: uppercase;
    font-size: 38px; letter-spacing: 1px;
  }
  .card--front .wordmark { top: 78px; color: var(--ink); }
  .card--back .wordmark { top: 96px; color: var(--paper); }

  .person { position: absolute; left: 20px; top: 160px; }
  .person__name { font-size: 16px; font-weight: 600; color: var(--ink); }
  .person__first { color: var(--green); }
  .person__role { font-size: 12.5px; color: var(--ink); margin-top: 2px; }

  .divider {
    position: absolute; left: 20px; right: 20px; top: 206px;
    height: 1.5px; background: var(--rule);
  }
  .contacts { position: absolute; left: 20px; top: 215px; list-style: none; }
  .contacts li {
    display: flex; align-items: center; gap: 8px;
    font-size: 12.5px; color: var(--ink); line-height: 16px;
  }
  .contacts svg { width: 8px; height: 8px; fill: var(--green); }

  .services {
    position: absolute; left: 0; right: 0; top: 215px;
    text-align: center; font-size: 12.5px; color: var(--paper);
    text-transform: uppercase;
  }
</style>
</head>
<body>
  <section class="card card--front">
    <p class="tagline">Live a life you don't need a holiday from</p>
    <p class="wordmark">Satchel &amp; Sundial</p>
    <div class="person">
      <p class="person__name"><span class="person__first">Dorota</span> Falkner</p>
      <p class="person__role">Your Lifestyle Business Coach ,Retreat &amp; Trip Leader</p>
    </div>
    <div class="divider"></div>
    <ul class="contacts">
      <li>
        <svg viewBox="0 0 8 8" aria-hidden="true"><rect x="0" y="1" width="8" height="6"/><path d="M0 1 L4 4.5 L8 1" stroke="#fff" stroke-width="0.8" fill="none"/></svg>
        hello@satchelandsundial.example
      </li>
      <li>
        <svg viewBox="0 0 8 8" aria-hidden="true"><circle cx="4" cy="4" r="4"/></svg>
        www.satchelandsundial.example
      </li>
    </ul>
  </section>

  <section class="card card--back">
    <p class="wordmark">Satchel &amp; Sundial</p>
    <p class="services">Coaching | Retreats | Trips</p>
  </section>
</body>
</html>
```